32 x 24 Swinging Real Estate Yard Sign

We are looking to design a new sign for our business to focus on the remodeling of homes to sell. We are looking to have a yard sign that gets peoples attention and is informational. The headline will be "The Secret to Top Dollar? Remodel First.". We remodel homes for sellers with no up front cost, as they simply pay at closing. This link has more info, https://bramblecresthomes.com/Remodel
The message we want to convey to those seeing the sign is we are a one stop shop, who can renovate your home and sell it for no stress. We are licensed real estate agents and licensed contractors.
Both of these license numbers and info need to be on the design:
CADRE #02794613
Contractors License #1178524
Email: info@bramblecresthomes.com
Phone: (408)614-2907
I'll attach a sample sign we have for our agents normally as well as all brand art work.
• Pantone Colors
o #172A41
Dark blue
o #4381B1
Medium blue
o #6FA6CC
Light blue
Target Market(s)
Residential Real Estate Sellers
Industry/Entity Type
Real Estate
Colors
Designer to choose colors to be used in the design.

```html
<!DOCTYPE html>
<html lang="en">
<head>
<meta charset="utf-8">
<title>Bramblecrest Yard Sign</title>
<link href="https://fonts.googleapis.com/css2?family=Montserrat:wght@300;400;500;600;700;800;900&display=swap" rel="stylesheet">
<style>
  :root {
    --navy: #172A41;
    --mid-blue: #4381B1;
    --light-blue: #6FA6CC;
    --white: #FFFFFF;
    --backdrop: #E9ECF0;
  }
  html, body {
    margin: 0;
    padding: 0;
    width: 1200px;
    height: 1200px;
    overflow: hidden;
    background: var(--backdrop);
    font-family: "Montserrat", sans-serif;
  }
  .yard-sign {
    position: absolute;
    left: 195px;
    top: 40px;
    width: 810px;
    height: 1120px;
    background: var(--navy);
    color: var(--white);
  }
  .brand {
    position: absolute;
    left: 71px;
    top: 112px;
    display: flex;
    align-items: center;
    gap: 22px;
  }
  .brand-dot {
    width: 58px;
    height: 58px;
    border-radius: 50%;
    background: var(--mid-blue);
    flex: none;
  }
  .brand-name {
    font-weight: 500;
    font-size: 66px;
    letter-spacing: 1px;
    line-height: 1;
    color: var(--white);
  }
  .agent-first {
    position: absolute;
    left: 66px;
    top: 458px;
    margin: 0;
    font-weight: 400;
    font-size: 166px;
    line-height: 1;
    letter-spacing: -2px;
  }
  .agent-last {
    position: absolute;
    left: 71px;
    top: 612px;
    margin: 0;
    font-weight: 900;
    font-size: 84px;
    line-height: 1;
    letter-spacing: -1px;
  }
  .agent-email {
    position: absolute;
    left: 71px;
    top: 702px;
    font-weight: 500;
    font-size: 35px;
    color: var(--mid-blue);
  }
  .headline {
    position: absolute;
    left: 71px;
    top: 786px;
    width: 680px;
    margin: 0;
    font-weight: 800;
    font-size: 38px;
    line-height: 1.15;
    color: var(--white);
  }
  .headline-accent {
    color: var(--light-blue);
  }
  .offer {
    position: absolute;
    left: 71px;
    top: 884px;
    width: 680px;
    margin: 0;
    font-weight: 500;
    font-size: 20px;
    line-height: 1.3;
    color: var(--light-blue);
  }
  .contact {
    position: absolute;
    left: 71px;
    top: 955px;
  }
  .contact-phone {
    display: block;
    font-weight: 700;
    font-size: 56px;
    line-height: 1.1;
    color: var(--mid-blue);
  }
  .contact-web {
    display: block;
    font-weight: 600;
    font-size: 31px;
    line-height: 1.3;
    color: var(--white);
  }
  .licenses {
    position: absolute;
    left: 585px;
    top: 958px;
    font-weight: 500;
    font-size: 17px;
    line-height: 1.3;
    color: var(--mid-blue);
    text-transform: uppercase;
  }
  .licenses p {
    margin: 0 0 26px;
  }
</style>
</head>
<body>
  <main class="yard-sign">
    <div class="brand">
      <span class="brand-dot"></span>
      <span class="brand-name">BRAMBLECREST</span>
    </div>

    <h1 class="agent-first">DANIEL</h1>
    <h2 class="agent-last">HARLOW</h2>
    <div class="agent-email">info@bramblecresthomes.com</div>

    <p class="headline">The Secret to Top Dollar? <span class="headline-accent">Remodel First.</span></p>
    <p class="offer">We renovate &amp; sell your home. No upfront cost &mdash; pay at closing.</p>

    <div class="contact">
      <span class="contact-phone">(408)614-2907</span>
      <span class="contact-web">bramblecresthomes.com</span>
    </div>

    <div class="licenses">
      <p>CADRE #02794613</p>
      <p>Contractors<br>License #1178524</p>
    </div>
  </main>
</body>
</html>
```